business card design for a plumbing contractor

i need a double business card for a plumbing business, our initial service is residential Sewer Drain Cleaning.

Target Market(s)

other plumbing Business

Industry/Entity Type

Plumbing

Contact Information for Business Card

www.PipeworksTopMark.example- 5307218394-

Font styles to use
Serif

Colors
ec1f27
0455a3

```html
<!DOCTYPE html>
<html lang="en">
<head>
<meta charset="utf-8">
<title>Pipeworks TopMark – Business Card</title>
<link href="https://fonts.googleapis.com/css2?family=Roboto+Condensed:wght@400;700&display=swap" rel="stylesheet">
<style>
  :root {
    --brand-red: #dc3a32;
    --ink-grey: #8a8884;
    --text-dark: #3a3a3a;
    --card-white: #f7f7f6;
    --page-bg: #e9e7e3;
    --on-red: #ffffff;
  }
  * { margin: 0; padding: 0; box-sizing: border-box; }
  html, body {
    width: 1200px; height: 886px; overflow: hidden;
    background: var(--page-bg);
    font-family: "Roboto Condensed", sans-serif;
  }
  .sheet {
    width: 1200px; height: 886px;
    display: flex; align-items: center; justify-content: center; gap: 60px;
  }
  .card {
    position: relative;
    width: 490px; height: 280px;
    border-radius: 18px;
    overflow: hidden;
    box-shadow: 0 6px 18px rgba(0,0,0,0.12);
  }
  /* Front */
  .card--front { background: var(--card-white); }
  .name-tab {
    position: absolute; top: 0; right: 0;
    width: 150px; height: 132px;
    background: var(--brand-red);
    color: var(--on-red);
    display: flex; flex-direction: column; justify-content: flex-end;
    padding: 0 0 18px 22px;
  }
  .name-tab__name { font-weight: 700; font-size: 21px; letter-spacing: 0.3px; line-height: 1.1; }
  .name-tab__title { font-weight: 400; font-size: 16px; line-height: 1.2; }
  .front-brand {
    position: absolute; left: 40px; top: 96px;
    display: flex; align-items: center; gap: 12px;
  }
  .brand-square { width: 18px; height: 18px; background: var(--brand-red); }
  .front-brand__name {
    font-weight: 700; font-size: 34px; line-height: 1; color: var(--ink-grey);
  }
  .contact-list {
    position: absolute; left: 40px; bottom: 28px;
    list-style: none;
    font-size: 14px; color: var(--text-dark); line-height: 1.55;
  }
  .contact-list li { display: flex; align-items: center; gap: 10px; }
  .contact-list svg { width: 11px; height: 11px; flex: none; }
  /* Back */
  .card--back {
    background: var(--brand-red); color: var(--on-red);
    display: flex; flex-direction: column; align-items: center; justify-content: center;
  }
  .service-line {
    position: absolute; left: 0; right: 0; text-align: center;
    font-size: 14px; letter-spacing: 0.3px;
  }
  .service-line--top { top: 40px; }
  .service-line--bottom { bottom: 40px; }
  .back-brand { display: flex; align-items: center; gap: 14px; }
  .back-brand .brand-square { background: var(--on-red); width: 22px; height: 22px; }
  .back-brand__name { font-weight: 700; font-size: 44px; line-height: 1; }
</style>
</head>
<body>
<main class="sheet">
  <section class="card card--front">
    <div class="name-tab">
      <span class="name-tab__name">DANA MORROW</span>
      <span class="name-tab__title">CEO/FOUNDER</span>
    </div>
    <div class="front-brand">
      <span class="brand-square"></span>
      <span class="front-brand__name">Pipeworks TopMark</span>
    </div>
    <ul class="contact-list">
      <li>
        <svg viewBox="0 0 12 12"><path d="M2.5 1 L4.5 1 L5.2 3.6 L4 4.6 Q5 7 7.4 8 L8.4 6.8 L11 7.5 L11 9.5 Q10 11 8.5 11 Q1 9.5 1 2.5 Q1 1 2.5 1Z" fill="var(--brand-red)"/></svg>
        5307218394
      </li>
      <li>
        <svg viewBox="0 0 12 12"><rect x="0.5" y="2" width="11" height="8" fill="var(--brand-red)"/><path d="M0.5 2 L6 6.5 L11.5 2" stroke="#fff" stroke-width="1" fill="none"/></svg>
        Dispatcher@PipeworksTopMark.example
      </li>
      <li>
        <svg viewBox="0 0 12 12"><circle cx="6" cy="6" r="5.5" fill="var(--brand-red)"/><path d="M0.5 6 H11.5 M6 0.5 Q3 6 6 11.5 M6 0.5 Q9 6 6 11.5" stroke="#fff" stroke-width="0.8" fill="none"/></svg>
        www.PipeworksTopMark.example
      </li>
    </ul>
  </section>

  <section class="card card--back">
    <p class="service-line service-line--top">Sewer Drain Cleaning</p>
    <div class="back-brand">
      <span class="brand-square"></span>
      <span class="back-brand__name">Pipeworks TopMark</span>
    </div>
    <p class="service-line service-line--bottom">Trenchless Pipe Installs</p>
  </section>
</main>
</body>
</html>
```